New Wix logo and website layout

I need a new logo design and a new, modern website layout design. I am a professional therapist providing remedial massage. I am Canadian but live in Australia & would like the logo to have a somewhat 'Canadian feel' to it (something subtle i.e. no flags) I currently have a maple tree leaf as my logo. my current website is tidewaterbodywork.com.au. I need the website to work on mobile phones & traditional web browsers.

Target Market(s)

customers looking for remedial massage and manual lymphatic drainage

Industry/Entity Type

professional massage

Coding

Coded - Design and coding required

Font styles to use
Sans Serif

Colors
EB3D1F
EC4F4E
F09395
F8D3D4
FCEDEE

Requirements
Nice to have
• something subtle that indicates that I am canadian
Should not have
• no flags. nothing too bold

```html
<!DOCTYPE html>
<html lang="en">
<head>
<meta charset="utf-8">
<title>Tidewater Bodywork</title>
<link rel="stylesheet" href="https://fonts.googleapis.com/css2?family=Noto+Serif:wght@400;700&family=Montserrat:wght@400;500;700&display=swap">
<style>
:root{
  --red:#EB3D1F;
  --red-soft:#EC4F4E;
  --pink:#F09395;
  --pink-light:#F8D3D4;
  --pink-pale:#FCEDEE;
  --ink:#222;
  --grey:#6b6b6b;
  --black:#000;
  --white:#fff;
}
*{box-sizing:border-box;margin:0;padding:0}
html,body{width:1200px;height:4370px;overflow:hidden}
body{position:relative;background:var(--white);font-family:"Noto Serif",serif;color:var(--ink)}
.abs{position:absolute}
.center{left:0;width:1200px;text-align:center}
.hero{top:0;left:0;width:1200px;height:760px;overflow:hidden;
  background:linear-gradient(100deg,#3a2a22 0%,#6e5848 30%,#b69a86 55%,#cfc0b2 75%,#8d7a6c 100%)}
.hero-circle{left:76px;top:115px;width:544px;height:544px;border-radius:50%;background:var(--pink-light);opacity:.95}
.brand{display:flex;align-items:center;gap:10px;color:var(--white);font-weight:700;font-size:20px;line-height:1.3;text-transform:uppercase}
.brand-dot{width:60px;height:60px;border-radius:50%;background:var(--red);flex:none}
.nav{top:46px;left:0;width:1200px;color:var(--white);font-size:15px;font-weight:700;text-transform:uppercase}
.nav span{position:absolute;top:0}
.hero-small{left:140px;top:232px;color:var(--red);font-size:42px;font-weight:700;line-height:1}
.hero-big{left:140px;top:284px;color:var(--red);font-size:72px;font-weight:700;line-height:78px}
.btn{display:flex;align-items:center;justify-content:center;background:var(--red);color:var(--white);font-size:20px;border-radius:5px;box-shadow:0 4px 10px rgba(0,0,0,.25);text-transform:uppercase}
.rule{left:599px;width:1.5px;background:var(--red)}
.mark{width:24px;height:24px;border-radius:50%;background:var(--red);left:588px}
.h2{color:var(--red);font-size:40px;font-weight:700;text-transform:uppercase}
.svc-label{width:300px;text-align:center;font-size:21px;color:var(--grey)}
.about-band{top:1707px;left:0;width:1200px;height:567px;
  background:linear-gradient(120deg,#f3d0d1 0%,#f6dcdc 40%,#ecc3c4 70%,#f5d7d8 100%)}
.about-lead{top:1902px;font-size:17px;font-weight:700;line-height:26px}
.about-body{top:1990px;font-size:17px;line-height:26px;color:#333}
.fees{left:98px;top:2500px;width:1007px;height:340px;background:var(--red);border-radius:8px;color:var(--white);font-size:20px}
.fee-row{position:absolute;left:24px;right:22px;display:flex;align-items:baseline;text-transform:uppercase}
.fee-row .dots{flex:1;border-bottom:2px dotted rgba(255,255,255,.85);margin:0 2px;transform:translateY(-4px)}
.rm-title{left:98px;top:3040px;font-size:40px;font-weight:700;color:var(--red);text-transform:uppercase}
.rm-body{left:102px;top:3124px;width:490px;font-size:17px;font-weight:700;line-height:25.8px}
.ben-title{left:626px;top:3046px;font-size:22px;font-weight:700;color:var(--red)}
.ben-list{left:626px;top:3090px;width:460px;list-style:none;font-size:15px;line-height:25.8px;color:#333}
.ben-list li{display:flex;gap:18px}
.ben-list svg{flex:none;margin-top:6px}
.photo{left:93px;top:3381px;width:990px;height:337px;border-radius:8px;
  background:radial-gradient(circle at 45% 15%,#e9b67d 0%,#8a4a2c 30%,#3a1d12 70%,#1e0e08 100%)}
.footer{left:0;top:3860px;width:1200px;height:510px}
.f-head{font-family:"Montserrat",sans-serif;font-size:19px;font-weight:700;color:var(--white)}
.f-text{font-family:"Montserrat",sans-serif;font-size:14px;line-height:22px;color:var(--white)}
.f-label{font-family:"Montserrat",sans-serif;font-size:13px;color:#ddd}
.email-box{left:811px;top:4092px;width:275px;height:38px;border-radius:19px;background:var(--white);font-family:"Montserrat",sans-serif;font-size:12px;color:#333;padding:12px 18px}
.send{position:absolute;right:10px;top:9px;width:20px;height:20px;border-radius:50%;background:var(--black)}
.social{width:30px;height:30px;border-radius:50%;border:1.5px solid var(--white)}
.copy{left:367px;top:4305px;font-family:"Montserrat",sans-serif;font-size:15px;color:var(--white)}
</style>
</head>
<body>

<header class="abs hero" role="img" aria-label="Photo of a couple relaxing on massage tables in a spa">
</header>
<div class="abs hero-circle"></div>
<svg class="abs" style="left:0;top:640px" width="1200" height="120" viewBox="0 640 1200 120">
  <path d="M0,675 Q520,775 1200,680 L1200,760 L0,760 Z" fill="#fff"/>
  <path d="M0,668 Q520,772 948,716" fill="none" stroke="#EB3D1F" stroke-width="9"/>
</svg>

<div class="abs brand" style="left:100px;top:18px">
  <span class="brand-dot"></span><span>Tidewater<br>Bodywork</span>
</div>
<nav class="abs nav">
  <span style="left:503px">Home</span>
  <span style="left:597px">Remedial Massage</span>
  <span style="left:811px">About Me</span>
  <span style="left:942px">Fees</span>
  <span style="left:1025px">Contact</span>
</nav>
<div class="abs hero-small">WELCOME TO</div>
<h1 class="abs hero-big">TIDEWATER<br>BODYWORK</h1>
<div class="abs btn" style="left:144px;top:460px;width:189px;height:49px">Get Started</div>

<!-- Services -->
<div class="abs rule" style="top:752px;height:105px"></div>
<div class="abs mark" style="top:816px"></div>
<h2 class="abs center h2" style="top:870px">Our Services</h2>

<svg class="abs" style="left:0;top:950px" width="1200" height="640">
  <g fill="none" stroke="#EB3D1F" stroke-width="8">
    <circle cx="285" cy="150" r="131" stroke-dasharray="640 183" transform="rotate(-30 285 150)"/>
    <circle cx="599" cy="150" r="131" stroke-dasharray="660 163" transform="rotate(-80 599 150)"/>
    <circle cx="913" cy="150" r="131" stroke-dasharray="620 203" transform="rotate(-150 913 150)"/>
    <circle cx="423" cy="487" r="131" stroke-dasharray="650 173" transform="rotate(100 423 487)"/>
    <circle cx="735" cy="487" r="131" stroke-dasharray="600 223" transform="rotate(-20 735 487)"/>
  </g>
  <circle cx="285" cy="150" r="110" fill="#b07459" role="img" aria-label="Deep tissue massage photo"/>
  <circle cx="599" cy="150" r="110" fill="#8f7868" role="img" aria-label="Remedial back massage photo"/>
  <circle cx="913" cy="150" r="110" fill="#6c6563" role="img" aria-label="Therapeutic exercise with a ring photo"/>
  <circle cx="423" cy="487" r="110" fill="#e4a27d" role="img" aria-label="Lymphatic drainage massage photo"/>
  <circle cx="735" cy="487" r="110" fill="#2a2220" role="img" aria-label="Pregnancy massage photo"/>
  <text x="735" y="477" text-anchor="middle" font-family="Montserrat,sans-serif" font-size="13.5" font-weight="500" fill="#fff">
    <tspan x="735" dy="-30">Lorem ipsum dolor sit</tspan>
    <tspan x="735" dy="19">amet, consectetur</tspan>
    <tspan x="735" dy="19">adipiscing elit, sed do</tspan>
    <tspan x="735" dy="19">eiusmod tempor</tspan>
    <tspan x="735" dy="19">incididunt ut labore</tspan>
  </text>
</svg>
<div class="abs svc-label" style="left:135px;top:1246px">Deep Tissue</div>
<div class="abs svc-label" style="left:449px;top:1244px">Remedial</div>
<div class="abs svc-label" style="left:763px;top:1248px">Therapeutic</div>
<div class="abs svc-label" style="left:273px;top:1584px">Lymphatic Drainage</div>
<div class="abs svc-label" style="left:585px;top:1584px;color:var(--red)">Pregnancy</div>

<div class="abs rule" style="top:1621px;height:86px"></div>

<!-- About -->
<section class="abs about-band" role="img" aria-label="Soft pink photo of hands giving a massage"></section>
<div class="abs mark" style="top:1770px"></div>
<h2 class="abs center h2" style="top:1838px">About Us</h2>
<p class="abs center about-lead">I completed my training in Toronto, Canada in 1999 where I obtained a Diploma of Remedial Massage<br>through the Northern College of Bodywork &amp; Hydrotherapy.</p>
<p class="abs center about-body">Over the years, I have practiced in several different settings including medical centre, chiropractic clinic, spa<br>and currently am a sole trader in my own practice. I have been helping my clients achieve better health<br>through my treatments for several years. I take special interest in women's health.</p>
<div class="abs btn" style="left:504px;top:2118px;width:188px;height:51px">Read More</div>
<div class="abs rule" style="top:2193px;height:124px"></div>

<!-- Fees -->
<div class="abs mark" style="top:2342px"></div>
<h2 class="abs center h2" style="top:2408px">Fee Schedule</h2>
<div class="abs fees">
  <div class="fee-row" style="top:34px"><span>30 min remedial massage</span><span class="dots"></span><span>$70</span></div>
  <div class="fee-row" style="top:86px"><span>45&nbsp; min remedial massage</span><span class="dots"></span><span>$90</span></div>
  <div class="fee-row" style="top:147px"><span>60 min&nbsp; remedial massage</span><span class="dots"></span><span>$110</span></div>
  <div class="fee-row" style="top:210px"><span>90 min remedial massage</span><span class="dots"></span><span>$140</span></div>
  <div class="fee-row" style="top:270px"><span>Manual lymphatic drainage</span><span class="dots"></span><span>$140</span></div>
</div>
<div class="abs rule" style="top:2840px;height:130px"></div>
<div class="abs mark" style="top:2978px"></div>

<!-- Remedial -->
<h2 class="abs rm-title">Remedial Massage</h2>
<p class="abs rm-body">Remedial massage is used to help relieve tension and stress in the soft tissues of the body including muscles, tendons, ligaments and connective tissue. It helps to alleviate soft tissue discomfort associated with everyday and occupational stress, over-use injuries e.g. tendinitis, and many chronic pain conditions.&nbsp; An increase in circulation and increased joint flexibility are additional benefits.</p>
<h3 class="abs ben-title">Other benefits include</h3>
<ul class="abs ben-list">
  <li><svg width="13" height="13" viewBox="0 0 13 13"><circle cx="6.5" cy="6.5" r="6.5" fill="#EB3D1F"/><path d="M3.5 6.7l2 2 4-4" stroke="#fff" stroke-width="1.6" fill="none"/></svg><span>Aids in recovery of sporting injuries</span></li>
  <li><svg width="13" height="13" viewBox="0 0 13 13"><circle cx="6.5" cy="6.5" r="6.5" fill="#EB3D1F"/><path d="M3.5 6.7l2 2 4-4" stroke="#fff" stroke-width="1.6" fill="none"/></svg><span>Improves joint mobility</span></li>
  <li><svg width="13" height="13" viewBox="0 0 13 13"><circle cx="6.5" cy="6.5" r="6.5" fill="#EB3D1F"/><path d="M3.5 6.7l2 2 4-4" stroke="#fff" stroke-width="1.6" fill="none"/></svg><span>Aids in the prevention of&nbsp; postural problems that are often associated with discomfort and pain</span></li>
  <li><svg width="13" height="13" viewBox="0 0 13 13"><circle cx="6.5" cy="6.5" r="6.5" fill="#EB3D1F"/><path d="M3.5 6.7l2 2 4-4" stroke="#fff" stroke-width="1.6" fill="none"/></svg><span>Reduces/prevents headaches</span></li>
  <li><svg width="13" height="13" viewBox="0 0 13 13"><circle cx="6.5" cy="6.5" r="6.5" fill="#EB3D1F"/><path d="M3.5 6.7l2 2 4-4" stroke="#fff" stroke-width="1.6" fill="none"/></svg><span>Assists with arthritic and rheumatic condition</span></li>
  <li><svg width="13" height="13" viewBox="0 0 13 13"><circle cx="6.5" cy="6.5" r="6.5" fill="#EB3D1F"/><path d="M3.5 6.7l2 2 4-4" stroke="#fff" stroke-width="1.6" fill="none"/></svg><span>Assists with pregnancy discomfort</span></li>
  <li><svg width="13" height="13" viewBox="0 0 13 13"><circle cx="6.5" cy="6.5" r="6.5" fill="#EB3D1F"/><path d="M3.5 6.7l2 2 4-4" stroke="#fff" stroke-width="1.6" fill="none"/></svg><span>Stimulates local blood supply and lymphatic fluids</span></li>
  <li><svg width="13" height="13" viewBox="0 0 13 13"><circle cx="6.5" cy="6.5" r="6.5" fill="#EB3D1F"/><path d="M3.5 6.7l2 2 4-4" stroke="#fff" stroke-width="1.6" fill="none"/></svg><span>Reduces levels of anxiety</span></li>
  <li><svg width="13" height="13" viewBox="0 0 13 13"><circle cx="6.5" cy="6.5" r="6.5" fill="#EB3D1F"/><path d="M3.5 6.7l2 2 4-4" stroke="#fff" stroke-width="1.6" fill="none"/></svg><span>Assists in stress management and times of grief</span></li>
</ul>
<div class="abs photo" role="img" aria-label="Warm candlelit photo of hands massaging a back"></div>
<div class="abs btn" style="left:506px;top:3754px;width:188px;height:51px">Read More</div>

<!-- Footer -->
<svg class="abs footer" width="1200" height="510" viewBox="0 3860 1200 510">
  <path d="M0,3972 Q600,3800 1200,3950 L1200,4370 L0,4370 Z" fill="#000"/>
  <path d="M120,3930 Q620,3830 1200,3950" fill="none" stroke="#EB3D1F" stroke-width="9"/>
  <line x1="110" y1="4268" x2="1088" y2="4268" stroke="#bbb" stroke-width="2"/>
</svg>
<div class="abs brand" style="left:112px;top:4075px;font-size:26px">
  <span class="brand-dot" style="width:70px;height:70px"></span><span>Tidewater<br>Bodywork</span>
</div>
<div class="abs f-head" style="left:467px;top:3970px">Contact Us</div>
<div class="abs" style="left:467px;top:4025px">
  <div class="f-label">ADDRESS</div>
  <div class="f-text"><svg width="10" height="13" viewBox="0 0 10 13"><path d="M5 0a5 5 0 0 0-5 5c0 4 5 8 5 8s5-4 5-8a5 5 0 0 0-5-5zm0 7a2 2 0 1 1 0-4 2 2 0 0 1 0 4z" fill="#fff"/></svg> Mara Ellis 24 Harbour Lane<br>Seacliff VIC 3199</div>
  <div class="f-label" style="margin-top:10px">PHONE</div>
  <div class="f-text"><svg width="12" height="12" viewBox="0 0 12 12"><path d="M2.5 0l2 3-1.2 1.3a8 8 0 0 0 4.4 4.4L9 7.5l3 2-1.5 2.5C5 12 0 7 0 1.5z" fill="#fff"/></svg> +61 0400 555 018</div>
  <div class="f-label" style="margin-top:10px">EMAIL</div>
  <div class="f-text"><svg width="14" height="10" viewBox="0 0 14 10"><rect width="14" height="10" rx="1" fill="#fff"/><path d="M0.5 0.5l6.5 5 6.5-5" stroke="#000" fill="none"/></svg> mara@tidewaterbodywork.com.au</div>
</div>
<div class="abs f-head" style="left:813px;top:3970px">Newsletter</div>
<div class="abs f-text" style="left:813px;top:4025px;width:290px">Lorem ipsum dolor sit amet, consectetur adipiscing elit, sed do eiusmod tempor</div>
<div class="abs email-box">Enter Email<span class="send"></span></div>
<div class="abs social" style="left:825px;top:4172px" role="img" aria-label="Professional network"></div>
<div class="abs social" style="left:862px;top:4172px" role="img" aria-label="Social page"></div>
<div class="abs social" style="left:900px;top:4172px" role="img" aria-label="Photo feed"></div>
<div class="abs" style="left:112px;top:4285px;width:60px;height:52px;border-radius:6px;background:#7fb23a" role="img" aria-label="Professional association badge"></div>
<div class="abs copy">© copyrights 2022 Tidewater Bodywork |&nbsp; All Rights Reserved</div>

</body>
</html>
```